BUSINESS CARD DESIGN

NAME- DALE VORSKIN
PHONE NUMER - 555- 714-9082
EMAIL- OFFICE@TRV-GROUNDMAKRZ.COM
BACK OF CARD- SPEACIALIZES IN LAND CLEARING, FORESTRY MUCLHING AND EXCAVATION

Contact Information for Business Card

NAME- DALE VORSKIN PHONE NUMER - 555- 714-9082 EMAIL- OFFICE@TRV-GROUNDMAKRZ.COM BACK OF CARD- SPEACIALIZES IN LAND CLEARING , MUCLHING AND EXCAVATION

```html
<!DOCTYPE html>
<html lang="en">
<head>
<meta charset="utf-8">
<title>Terravale Groundmakrz – Business Card</title>
<link href="https://fonts.googleapis.com/css2?family=Orbitron:wght@700;800&family=Open+Sans:wght@400;600&display=swap" rel="stylesheet">
<style>
  :root {
    --page: #e4e5e7;
    --card: #ffffff;
    --ink: #111111;
    --accent: #f5b400;
    --muted: #555555;
    --palm-dark: #1a1a1a;
    --palm-light: #4a4a4a;
  }
  * { margin: 0; padding: 0; box-sizing: border-box; }
  html, body { width: 1200px; height: 800px; overflow: hidden; }
  body {
    background: var(--page);
    display: flex;
    flex-direction: column;
    align-items: center;
    justify-content: center;
    gap: 32px;
    font-family: "Open Sans", Arial, sans-serif;
  }
  .card {
    position: relative;
    width: 620px;
    height: 354px;
    background: var(--card);
    box-shadow: 0 6px 18px rgba(0,0,0,0.12);
    overflow: hidden;
  }
  .card__band {
    position: absolute;
    left: 0; right: 0;
    top: 292px;
    height: 16px;
    background: var(--ink);
  }
  .palms {
    position: absolute;
    background: linear-gradient(180deg, var(--palm-light) 0%, var(--palm-dark) 70%);
    border-radius: 46% 46% 6px 6px;
  }
  .brand {
    display: flex;
    align-items: center;
    gap: 10px;
    position: absolute;
  }
  .brand__mark {
    width: 40px; height: 40px;
    border-radius: 50%;
    background: var(--ink);
    flex: none;
  }
  .brand__name {
    font-family: "Orbitron", "Arial Black", sans-serif;
    font-weight: 800;
    font-size: 13px;
    line-height: 1.25;
    color: var(--ink);
    letter-spacing: 0.5px;
  }
  /* Front */
  .card--front .brand { left: 56px; top: 40px; }
  .holder {
    position: absolute;
    left: 56px; top: 122px;
    font-family: "Orbitron", "Arial Black", sans-serif;
    font-weight: 800;
    font-size: 24px;
    color: var(--accent);
    letter-spacing: 0.5px;
  }
  .contact {
    position: absolute;
    left: 56px; top: 168px;
    list-style: none;
    color: var(--muted);
    font-size: 15px;
  }
  .contact__item { display: flex; align-items: center; gap: 9px; margin-bottom: 6px; }
  .contact__icon { width: 14px; height: 14px; fill: var(--accent); flex: none; }
  .card--front .palms { left: 360px; top: 118px; width: 240px; height: 176px; }
  /* Back */
  .card--back .palms { left: 60px; top: 90px; width: 190px; height: 204px; }
  .card--back .brand { left: 320px; top: 130px; }
  .specialty {
    position: absolute;
    left: 320px; top: 200px;
  }
  .specialty__title {
    font-family: "Orbitron", "Arial Black", sans-serif;
    font-weight: 800;
    font-size: 20px;
    color: var(--accent);
    letter-spacing: 0.5px;
  }
  .specialty__list {
    margin-top: 6px;
    font-size: 15px;
    color: var(--muted);
  }
</style>
</head>
<body>
  <section class="card card--front">
    <div class="brand">
      <span class="brand__mark"></span>
      <span class="brand__name">TERRAVALE<br>GROUNDMAKRZ LLC</span>
    </div>
    <h1 class="holder">DALE VORSKIN</h1>
    <ul class="contact">
      <li class="contact__item">
        <svg class="contact__icon" viewBox="0 0 24 24" aria-hidden="true"><path d="M6.6 10.8a15.5 15.5 0 0 0 6.6 6.6l2.2-2.2a1 1 0 0 1 1-.25 11.4 11.4 0 0 0 3.6.57 1 1 0 0 1 1 1V20a1 1 0 0 1-1 1A17 17 0 0 1 3 4a1 1 0 0 1 1-1h3.5a1 1 0 0 1 1 1c0 1.25.2 2.45.57 3.57a1 1 0 0 1-.25 1z"/></svg>
        555- 714-9082
      </li>
      <li class="contact__item">
        <svg class="contact__icon" viewBox="0 0 24 24" aria-hidden="true"><path d="M2 5h20v14H2z M3.5 6.5 12 13l8.5-6.5" fill="none" stroke="#f5b400" stroke-width="2.4"/></svg>
        office@trv-groundmakrz.com
      </li>
    </ul>
    <div class="palms" role="img" aria-label="Black silhouette of two palm trees"></div>
    <div class="card__band"></div>
  </section>

  <section class="card card--back">
    <div class="palms" role="img" aria-label="Black silhouette of two palm trees"></div>
    <div class="brand">
      <span class="brand__mark"></span>
      <span class="brand__name">TERRAVALE<br>GROUNDMAKRZ LLC</span>
    </div>
    <div class="specialty">
      <h2 class="specialty__title">SPEACIALIZES IN</h2>
      <p class="specialty__list">Land Clearing, Muclhing And Excavation</p>
    </div>
    <div class="card__band"></div>
  </section>
</body>
</html>
```